Tolbek cards

I want a simple business card that pops.
Logo on one side.
On side two i want.
"Are you thinking about a new building on your property, or renovating an existing structure? Contact".....
Owners Name: Dale Whitacre
Owners Phone number: 610-555-0187
Address:4076 Copper Ridge RD, Ashford, PA 16734
Committed to Quality, Service, and Integrity

```html
<!DOCTYPE html>
<html lang="en">
<head>
<meta charset="utf-8">
<title>Tolbek Builders – Business Card</title>
<link rel="stylesheet" href="https://fonts.googleapis.com/css2?family=Oswald:wght@600&family=Montserrat:wght@600;700;800&family=Poppins:wght@300&display=swap">
<style>
  :root {
    --brown: #3f2d1d;
    --tan: #eecda5;
    --tan-deep: #d9b68c;
    --white: #ffffff;
    --backdrop: #b6b6b6;
  }
  * { margin: 0; padding: 0; box-sizing: border-box; }
  html, body { width: 1200px; height: 1200px; overflow: hidden; }
  body { background: var(--backdrop); position: relative; }

  .card { position: absolute; top: 303px; width: 368px; height: 593px; overflow: hidden; }

  /* Front */
  .card-front { left: 201px; background: var(--tan); }
  .tower-photo {
    position: absolute; inset: 0;
    background:
      radial-gradient(ellipse 45% 70% at 42% 60%, rgba(160,120,80,0.35), rgba(238,205,165,0) 70%),
      linear-gradient(180deg, var(--tan) 0%, #e2bf95 60%, var(--tan-deep) 100%);
  }
  .brand {
    position: absolute; left: 0; right: 0; top: 455px;
    text-align: center; color: var(--brown);
    font-family: 'Montserrat', sans-serif;
  }
  .brand-name { display: block; font-weight: 800; font-size: 54px; line-height: 52px; letter-spacing: 0.5px; }
  .brand-sub { display: block; font-weight: 600; font-size: 18px; line-height: 24px; letter-spacing: 2.5px; margin-top: 1px; }

  /* Back */
  .card-back { left: 599px; background: var(--white); }
  .question {
    position: absolute; left: 0; right: 0; top: 42px;
    text-align: center; color: var(--brown);
    font-family: 'Oswald', sans-serif; font-weight: 600;
    font-size: 30px; line-height: 42px; text-transform: uppercase;
  }
  .back-shape { position: absolute; left: 0; top: 0; width: 368px; height: 593px; }

  .contact { position: absolute; left: 0; right: 0; top: 348px; text-align: center; color: var(--white); }
  .contact-label {
    display: flex; align-items: center; justify-content: center; gap: 8px;
    font-family: 'Poppins', sans-serif; font-weight: 300; font-size: 18px; line-height: 26px;
  }
  .contact-label::before, .contact-label::after { content: ""; width: 85px; height: 1px; background: var(--white); }
  .owner-name { font-family: 'Montserrat', sans-serif; font-weight: 600; font-size: 24px; line-height: 32px; margin-top: 2px; }
  .owner-phone { font-family: 'Poppins', sans-serif; font-weight: 300; font-size: 18px; line-height: 24px; }
  .divider-short { width: 38px; height: 1px; background: rgba(255,255,255,0.6); margin: 6px auto 6px; }
  .address { font-family: 'Poppins', sans-serif; font-weight: 300; font-size: 18px; line-height: 23px; font-style: normal; }
  .divider-long { width: 265px; height: 1px; background: var(--white); margin: 13px auto 0; }
  .tagline {
    font-family: 'Oswald', sans-serif; font-weight: 600; font-size: 17px; line-height: 24px;
    text-transform: uppercase; margin-top: 10px; letter-spacing: -0.2px;
  }
</style>
</head>
<body>
  <section class="card card-front">
    <div class="tower-photo" role="img" aria-label="Faded warm-toned photo of a tall curved residential tower seen from below"></div>
    <div class="brand">
      <span class="brand-name">TOLBEK</span>
      <span class="brand-sub">BUILDERS LLC</span>
    </div>
  </section>

  <section class="card card-back">
    <svg class="back-shape" viewBox="0 0 368 593" aria-hidden="true">
      <rect x="0" y="281" width="368" height="312" fill="var(--brown)"/>
      <rect x="0" y="275" width="368" height="2" fill="var(--brown)"/>
      <polygon points="125,281 181,219 238,281" fill="var(--brown)"/>
      <polygon points="166,281 181,264 196,281" fill="var(--white)"/>
    </svg>
    <h1 class="question">Are you thinking about<br>a new building on your<br>property, or renovating<br>an existing structure?</h1>
    <div class="contact">
      <p class="contact-label">Contact</p>
      <p class="owner-name">DALE WHITACRE</p>
      <p class="owner-phone">610-555-0187</p>
      <div class="divider-short"></div>
      <address class="address">4076 Copper Ridge RD,<br>Ashford, PA 16734</address>
      <div class="divider-long"></div>
      <p class="tagline">Committed to quality, service and integrity</p>
    </div>
  </section>
</body>
</html>
```